Corvane Holdings , new business card design

investment firm with corporate clients . need double sided business card , vertical and horizontal options ,logo must be clear. prefer pantone colors only and sharp design. website also www.corvane.ae

Khalid Bin Tarrafi
Managing Director
Tel. +971 4 387 2940
Mobile +971 50 518 2403
khalid@corvane.ae
Q-Span Plaza, officw 18-B07, Warqa Gardens, Dubai

Contact Information for Business Card

Khalid Bin Tarrafi
Managing Director

Font styles to use
Serif

Colors

Designer to choose colors to be used in the design.

```html
<!DOCTYPE html>
<html lang="en">
<head>
<meta charset="utf-8">
<title>Corvane Holdings – Business Card</title>
<link rel="stylesheet" href="https://fonts.googleapis.com/css2?family=Jost:wght@300&family=Roboto:wght@400;500&family=Roboto+Condensed:wght@700&display=swap">
<style>
  :root {
    --backdrop: #dedede;
    --card-white: #f4f4f4;
    --brand-blue: #436d92;
    --ink: #1c1c1c;
    --text-grey: #4a4a4a;
    --rule-grey: #9a9a9a;
    --white: #ffffff;
  }
  * { margin: 0; padding: 0; box-sizing: border-box; }
  html, body {
    width: 1200px; height: 960px; overflow: hidden;
    background: var(--backdrop);
  }
  .card {
    position: absolute;
    width: 602px; height: 342px;
  }
  .card--front { left: 315px; top: 113px; background: var(--card-white); }
  .card--back  { left: 311px; top: 472px; background: var(--brand-blue); }

  .wordmark {
    position: absolute;
    font-family: 'Jost', sans-serif;
    font-weight: 300;
    text-align: center;
    line-height: 1;
  }
  .wordmark__name { display: block; font-size: 44px; letter-spacing: 0.36em; margin-right: -0.36em; }
  .wordmark__sub  { display: block; font-size: 13px; letter-spacing: 0.98em; margin-right: -0.98em; margin-top: 6px; }
  .card--front .wordmark { right: 38px; top: 44px; color: var(--ink); }
  .card--back .wordmark { left: 0; right: 0; top: 134px; color: var(--white); }
  .card--back .wordmark__name { font-size: 46px; }

  .accent-bar {
    position: absolute; left: 0; top: 171px;
    width: 14px; height: 38px; background: var(--brand-blue);
  }
  .holder { position: absolute; left: 37px; top: 168px; }
  .holder__name {
    font-family: 'Roboto Condensed', sans-serif; font-weight: 700;
    font-size: 21px; color: var(--brand-blue); line-height: 26px;
  }
  .holder__title {
    font-family: 'Roboto', sans-serif; font-weight: 500;
    font-size: 15px; color: var(--ink); line-height: 20px; letter-spacing: 0.01em;
  }
  .divider {
    position: absolute; left: 37px; top: 221px; width: 526px;
    height: 1px; background: var(--rule-grey);
  }
  .contact-list {
    position: absolute; left: 37px; top: 238px; list-style: none;
    font-family: 'Roboto', sans-serif; font-size: 14.5px; color: var(--text-grey);
  }
  .contact-list li { display: flex; align-items: center; height: 19px; }
  .contact-list svg { width: 13px; height: 13px; margin-right: 7px; fill: var(--brand-blue); }
  .address {
    position: absolute; right: 39px; top: 276px; text-align: right;
    font-family: 'Roboto', sans-serif; font-size: 14.5px; line-height: 19px; color: var(--text-grey);
  }
  .back-url {
    position: absolute; left: 0; right: 0; top: 289px; text-align: center;
    font-family: 'Roboto', sans-serif; font-size: 14px; color: var(--white);
    letter-spacing: 0.75em; margin-right: -0.75em;
  }
</style>
</head>
<body>
  <section class="card card--front">
    <div class="wordmark">
      <span class="wordmark__name">CORVANE</span>
      <span class="wordmark__sub">HOLDINGS</span>
    </div>
    <div class="accent-bar"></div>
    <div class="holder">
      <p class="holder__name">KHALID BIN TARRAFI</p>
      <p class="holder__title">MANAGING DIRECTOR</p>
    </div>
    <div class="divider"></div>
    <ul class="contact-list">
      <li><svg viewBox="0 0 16 16" aria-hidden="true"><path d="M3.5 1 6 4.2 4.6 6.1c.8 2 2.3 3.5 4.3 4.3l1.9-1.4L14 11.5 12.6 14C6.6 13.7 2.3 9.4 2 3.4Z"/></svg>+971 4 387 2940</li>
      <li><svg viewBox="0 0 16 16" aria-hidden="true"><path d="M4 1h8v14H4Zm1.5 1.5v9.5h5V2.5Z"/></svg>+971 50 518 2403</li>
      <li><svg viewBox="0 0 16 16" aria-hidden="true"><path d="M1 3.5h14v1L8 9 1 4.5Zm0 2.6 7 4.4 7-4.4V13H1Z"/></svg>khalid@corvane.ae</li>
      <li><svg viewBox="0 0 16 16" aria-hidden="true"><path d="M8 1a7 7 0 1 0 0 14A7 7 0 0 0 8 1Zm-1 2.2L5.5 5.5 7 7.5 6 10l2 2.7V14A6 6 0 0 1 3.3 4.6Zm3 .3 2.7 1.2.8 3.3-2 .3-1.5-2-1-.8Z"/></svg>www.corvane.ae</li>
    </ul>
    <address class="address" style="font-style:normal">Q-Span Plaza, officw 18-B07<br>Warqa Gardens, Dubai</address>
  </section>

  <section class="card card--back">
    <div class="wordmark">
      <span class="wordmark__name">CORVANE</span>
      <span class="wordmark__sub">HOLDINGS</span>
    </div>
    <p class="back-url">www.corvane.ae</p>
  </section>
</body>
</html>
```